Design and Renovation Company Luxury Business Card

I want to create a luxury business card for a Design and Renovation Firm . We will use our current logo. The company name is 528BUILDA. We do not want anything standard. We need a very unique concept.
Please see uploaded inspiration. I really like the textured paper option. I would like the card to be thick with debossing, and/or embossing options. The logo has orange in it but I would like to see the card with and without the orange. I think the orange may make the company feel less high-end. The goal is to elevate the logo not match its vibe per se of the logo. We want something very unique, not standard at all!
I would like a space for :
Logo,
Name,
Position,
Email,
Office number,
Website Address,
Business Address,
Thank you!
Have fun!
Target Market(s)
Home owners Age 35 +
Industry/Entity Type
Design and Renovation
Contact Information for Business Card
Logo, Name, Position, Email, Office number, Website Address, Business Address,.
Colors
Designer to choose colors to be used in the design.
Requirements
Must have
- A luxury designer feel. Must be black or dark grey but open to other luxury ideas.
Nice to have
- Gold, silver, black embossing or debossing. Textured paper design.
Should not have
- A cheap look and feel.

```html
<!DOCTYPE html>
<html lang="en">
<head>
<meta charset="utf-8">
<title>528BUILDA Business Card</title>
<link rel="stylesheet" href="https://fonts.googleapis.com/css2?family=Montserrat:wght@500;700&family=Lato:wght@400&display=swap">
<style>
  :root {
    --backdrop: #2c2c2c;
    --card: #232323;
    --gold: #d9a53a;
    --gold-light: #e8c45a;
    --gold-deep: #c8892c;
    --rule: #5a4722;
  }
  * { margin: 0; padding: 0; box-sizing: border-box; }
  html, body {
    width: 1200px;
    height: 900px;
    overflow: hidden;
    background: var(--backdrop);
  }
  .canvas {
    position: relative;
    width: 1200px;
    height: 900px;
  }
  .card {
    position: absolute;
    left: 329px;
    width: 474px;
    height: 271px;
    background: var(--card);
    box-shadow: 0 6px 14px rgba(0,0,0,0.55);
  }
  .card-front { top: 156px; }
  .card-back { top: 473px; }

  .company-name {
    font-family: "Montserrat", sans-serif;
    font-weight: 500;
    color: var(--gold);
    letter-spacing: 0.14em;
    line-height: 1;
    white-space: nowrap;
  }

  /* Front */
  .front-name {
    position: absolute;
    left: 0;
    right: 0;
    top: 120px;
    text-align: center;
    font-size: 30px;
  }

  /* Back */
  .back-name {
    position: absolute;
    left: 72px;
    top: 170px;
    font-size: 14px;
    letter-spacing: 0.1em;
  }
  .divider {
    position: absolute;
    left: 196px;
    top: 54px;
    width: 1px;
    height: 146px;
    background: var(--rule);
  }
  .person {
    position: absolute;
    left: 222px;
    top: 72px;
  }
  .person-name {
    font-family: "Montserrat", sans-serif;
    font-weight: 500;
    font-size: 15px;
    letter-spacing: 0.06em;
    color: var(--gold-light);
    line-height: 1.15;
  }
  .person-name strong { font-weight: 700; }
  .person-role {
    font-family: "Lato", sans-serif;
    font-size: 12.5px;
    color: var(--gold-light);
    margin-top: 1px;
  }
  .contact-list {
    position: absolute;
    left: 222px;
    top: 125px;
    list-style: none;
  }
  .contact-item {
    display: flex;
    align-items: center;
    gap: 5px;
    height: 20px;
    font-family: "Lato", sans-serif;
    font-size: 12px;
    color: var(--gold-light);
  }
  .contact-icon {
    width: 10px;
    height: 10px;
    flex: none;
  }
  .address {
    position: absolute;
    left: 74px;
    top: 223px;
    font-family: "Lato", sans-serif;
    font-size: 10.5px;
    color: var(--gold-deep);
  }
</style>
</head>
<body>
<main class="canvas">
  <section class="card card-front">
    <p class="company-name front-name">528BUILDA</p>
  </section>

  <section class="card card-back">
    <p class="company-name back-name">528BUILDA</p>
    <div class="divider"></div>
    <div class="person">
      <p class="person-name">DANIEL M. <strong>HARLOW</strong></p>
      <p class="person-role">Managing Director</p>
    </div>
    <ul class="contact-list">
      <li class="contact-item">
        <svg class="contact-icon" viewBox="0 0 10 10"><path d="M2 0.8 L3.6 2.8 L2.8 3.8 Q4 6.2 6.2 7.2 L7.2 6.4 L9.2 8 L8 9.4 Q3.8 9 0.8 2 Z" fill="var(--gold)"/></svg>
        <span>+00 987 654 32</span>
      </li>
      <li class="contact-item">
        <svg class="contact-icon" viewBox="0 0 10 10"><rect x="0.5" y="2" width="9" height="6.5" fill="var(--gold)"/><path d="M0.8 2.3 L5 5.6 L9.2 2.3" fill="none" stroke="var(--card)" stroke-width="1"/></svg>
        <span>studio@528builda.com</span>
      </li>
      <li class="contact-item">
        <svg class="contact-icon" viewBox="0 0 10 10"><circle cx="5" cy="5" r="4.2" fill="none" stroke="var(--gold)" stroke-width="1"/><ellipse cx="5" cy="5" rx="1.8" ry="4.2" fill="none" stroke="var(--gold)" stroke-width="0.8"/><line x1="0.8" y1="5" x2="9.2" y2="5" stroke="var(--gold)" stroke-width="0.8"/></svg>
        <span>www.528builda.com</span>
      </li>
    </ul>
    <p class="address">1742 Lakeview Avenue Portland, OR 97205</p>
  </section>
</main>
</body>
</html>
```